Marwick Jewelers New Website Design

This project is to provide a new design for an existing website. The existing website is marwickjewelers dot com . I have created a overview document that outlines all the details for the project. I do not need the design to be converted into HTML. I have a team for that already so please don't ask. I have a lot of images .. too many to upload here so they are on my dev server located at quillfoxstudio com slash marwick slash assets

Number of Pages Required

1 page

```html
<!DOCTYPE html>
<html lang="en">
<head>
<meta charset="utf-8">
<title>Marwick Jewelers</title>
<link href="https://fonts.googleapis.com/css2?family=Merriweather:wght@400;700&family=Nunito:wght@400;600&display=swap" rel="stylesheet">
<style>
:root{
  --teal:#5a979f;
  --teal-dark:#4b8992;
  --teal-text:#4f929b;
  --pale:#e3f1f4;
  --card-label:#e2f0f2;
  --field:#f2f3f4;
  --ink:#2f3a3d;
  --white:#ffffff;
  --footer:#434445;
  --footer-text:#e9e9e9;
}
*{box-sizing:border-box;margin:0;padding:0}
html,body{width:1200px;height:3518px;overflow:hidden}
body{font-family:"Nunito",sans-serif;color:var(--ink);background:var(--white);position:relative}

/* top bar */
.topbar{position:absolute;top:0;left:0;width:1200px;height:44px;background:var(--teal);color:var(--white);font-size:15px}
.topbar .links{position:absolute;left:109px;top:11px;display:flex;gap:32px}
.topbar .phone{position:absolute;right:178px;top:10px;display:flex;align-items:center;gap:10px;font-size:17px}
.topbar .divider{position:absolute;right:155px;top:8px;width:1px;height:26px;background:rgba(255,255,255,.45)}
.topbar .search{position:absolute;right:110px;top:10px}

.navbar{position:absolute;top:44px;left:0;width:1200px;height:61px;background:var(--white);font-size:15.5px}
.navbar a{position:absolute;top:21px;color:var(--ink);text-decoration:none}
.navbar a.active{color:var(--teal-text)}

.logo-tab{position:absolute;top:0;left:488px;width:224px;height:123px;z-index:3}
.logo-name{position:absolute;top:60px;left:0;width:224px;text-align:center;font-family:"Merriweather",serif;font-size:32px;color:#4b4f52}

/* hero */
.hero{position:absolute;top:105px;left:0;width:1200px;height:597px;background:linear-gradient(135deg,#5f9ea6 0%,#4f8f98 60%,#4a8890 100%);overflow:hidden}
.hero .blob1{position:absolute;left:-120px;top:-210px;width:420px;height:420px;border-radius:50%;background:rgba(40,90,98,.35)}
.hero .blob2{position:absolute;left:-140px;top:260px;width:400px;height:400px;border-radius:50%;background:rgba(40,90,98,.25)}
.hero .blob3{position:absolute;left:1010px;top:-20px;width:440px;height:500px;border-radius:50%;background:rgba(40,90,98,.35)}
.hero h2{position:absolute;left:108px;top:180px;font-family:"Merriweather",serif;font-weight:400;font-size:44px;color:var(--white)}
.hero h1{position:absolute;left:106px;top:248px;font-family:"Merriweather",serif;font-weight:400;font-size:64px;color:var(--white);white-space:nowrap}
.hero .btn{position:absolute;left:110px;top:350px;width:166px;height:62px;border:2px solid var(--white);color:var(--white);font-size:19px;display:flex;align-items:center;justify-content:center}
.hero .ring{position:absolute;left:760px;top:185px;width:330px;height:290px;border-radius:45%;background:radial-gradient(circle at 50% 55%,#c1334f 0 15%,#f2c2a7 16% 42%,rgba(240,170,140,.5) 43% 68%,transparent 70%)}
.dots{position:absolute;left:111px;top:548px;display:flex;gap:20px}
.dots span{width:15px;height:15px;border-radius:50%;background:var(--white)}
.dots span.on{background:transparent;border:2px solid var(--white)}
.social{display:flex;gap:14px}
.social span{width:37px;height:37px;border-radius:50%;border:2px solid var(--white);display:flex;align-items:center;justify-content:center}
.social span i{width:8px;height:8px;border-radius:50%;background:var(--white)}
.hero .social{position:absolute;left:1000px;top:537px}

/* sections */
.section-title{position:absolute;left:0;width:1200px;text-align:center;font-family:"Merriweather",serif;font-weight:400;font-size:44px;color:var(--teal-text)}
.cards{position:absolute;left:109px;display:flex;gap:21px}
.card{width:229px;background:var(--white);box-shadow:0 3px 8px rgba(0,0,0,.12);position:relative}
.card .photo{height:241px}
.card .label{height:85px;background:var(--card-label);display:flex;align-items:center;justify-content:center;text-align:center;font-size:17px;line-height:28px;padding:0 18px}
.card.hover .label{background:var(--teal);color:var(--white)}
.card .overlay-btn{position:absolute;left:34px;top:140px;width:162px;height:58px;background:var(--teal);color:var(--white);font-size:19px;display:flex;align-items:center;justify-content:center}

.about{position:absolute;top:1313px;left:0;width:1200px;height:549px;background:linear-gradient(180deg,#5a979f,#4a8690)}
.about .ring-back{position:absolute;left:102px;top:88px;width:382px;height:382px;border-radius:50%;background:#6aa5ad}
.about .photo{position:absolute;left:112px;top:88px;width:373px;height:373px;border-radius:50%;background:radial-gradient(circle at 52% 45%,#e9e3d6 0 12%,#6d6d6d 13% 30%,#111 55%)}
.about h2{position:absolute;left:618px;top:83px;font-family:"Merriweather",serif;font-weight:400;font-size:43px;color:var(--white)}
.about h3{position:absolute;left:589px;top:159px;font-family:"Merriweather",serif;font-weight:400;font-size:22px;color:var(--white)}
.about .copy{position:absolute;left:589px;top:216px;width:500px;color:var(--white);font-size:17.5px;line-height:28.4px;text-align:justify}
.about .copy p+p{margin-top:18px}

.contact{position:absolute;top:2476px;left:0;width:1200px;height:713px;background:var(--pale)}
.contact .watch{position:absolute;left:75px;top:308px;width:178px;height:385px;border-radius:80px;background:linear-gradient(180deg,#d9c2c2,#efe9ee 45%,#c9b1b4)}
.contact .box{position:absolute;left:224px;top:90px;width:752px;height:529px;background:var(--white)}
.contact h2{position:absolute;left:0;top:32px;width:752px;text-align:center;font-family:"Merriweather",serif;font-weight:700;font-size:32px;color:var(--teal-text)}
.field{position:absolute;background:var(--field);color:#777;font-size:22px;padding:20px 35px}
.contact .submit{position:absolute;left:295px;top:443px;width:163px;height:58px;background:var(--teal);color:var(--white);font-size:19px;display:flex;align-items:center;justify-content:center}

.footer{position:absolute;top:3189px;left:0;width:1200px;height:329px;background:var(--footer);color:var(--footer-text);font-size:15.5px}
.footer .col{position:absolute;top:68px}
.footer h4{font-family:"Merriweather",serif;font-weight:700;font-size:15px;color:var(--white);margin-bottom:12px;letter-spacing:.2px}
.footer li{list-style:none;line-height:30px}
.footer .contact-list li{line-height:38px;font-size:17px;display:flex;align-items:center;gap:8px}
.footer .rule{position:absolute;left:109px;top:266px;width:980px;height:1px;background:rgba(255,255,255,.12)}
.footer .copy{position:absolute;left:109px;top:285px;font-size:16px}
.footer .social{position:absolute;left:1022px;top:279px;gap:10px}
.footer .social span{width:28px;height:28px;border-width:1.5px}
.footer .social span i{width:6px;height:6px}
</style>
</head>
<body>

<header>
  <div class="topbar">
    <div class="links"><span>Resources</span><span>Showcase</span><span>Engraving &amp; Trophies</span></div>
    <div class="phone">
      <svg width="20" height="20" viewBox="0 0 24 24"><path fill="#fff" d="M6.6 10.8a15 15 0 0 0 6.6 6.6l2.2-2.2c.3-.3.7-.4 1-.2 1.1.4 2.3.6 3.6.6.6 0 1 .4 1 1V20c0 .6-.4 1-1 1A17 17 0 0 1 3 4c0-.6.4-1 1-1h3.5c.6 0 1 .4 1 1 0 1.3.2 2.5.6 3.6.1.3 0 .7-.2 1z"/></svg>
      <span>+1-800-555-0142</span>
    </div>
    <div class="divider"></div>
    <svg class="search" width="22" height="22" viewBox="0 0 24 24" fill="none" stroke="#fff" stroke-width="2"><circle cx="10" cy="10" r="7"/><path d="M15 15l6 6"/></svg>
  </div>
  <nav class="navbar">
    <a class="active" style="left:109px">Home</a>
    <a style="left:188px">Company</a>
    <a style="left:293px">Custom Jewelery Services ▾</a>
    <a style="left:715px">Jewelery Repair Services</a>
    <a style="left:930px">Gallery</a>
    <a style="left:1021px">Gift Ideas</a>
  </nav>
  <div class="logo-tab">
    <svg width="224" height="123" viewBox="0 0 224 123" style="position:absolute;left:0;top:0"><polygon points="20,0 204,0 224,44 200,123 24,123 0,44" fill="#fff"/></svg>
    <div class="logo-name">Marwick</div>
  </div>
</header>

<section class="hero">
  <div class="blob1"></div><div class="blob2"></div><div class="blob3"></div>
  <h2>Welcome To</h2>
  <h1>Marwick Jewellery</h1>
  <div class="btn">Contact Us</div>
  <div class="ring" role="img" aria-label="Rose gold ring with a ruby centre stone and diamond halo"></div>
  <div class="dots"><span class="on"></span><span></span><span></span></div>
  <div class="social"><span><i></i></span><span><i></i></span></div>
</section>

<section>
  <h2 class="section-title" style="top:776px">Featured Products</h2>
  <div class="cards" style="top:880px">
    <div class="card"><div class="photo" role="img" aria-label="White gold ring with a pearl" style="background:radial-gradient(circle at 50% 55%,#f4f1f4 0 12%,#d9d2dc 13% 32%,#fff 45%)"></div><div class="label">Gold Pearl Ring</div></div>
    <div class="card"><div class="photo" role="img" aria-label="Gold ring set with diamonds" style="background:radial-gradient(circle at 50% 55%,#a59a90 0 14%,#e8c9a0 15% 32%,#fff 45%)"></div><div class="label">Gold Diamond Ring</div></div>
    <div class="card hover"><div class="photo" role="img" aria-label="Gold and diamond bracelet" style="background:radial-gradient(ellipse 45% 20% at 50% 45%,#fff 0 80%,#c7bcbd 85%,#fff 100%)"></div><div class="overlay-btn">Contact Us</div><div class="label">Gold + Diamond Bracelets</div></div>
    <div class="card"><div class="photo" role="img" aria-label="Steel wristwatch" style="background:linear-gradient(90deg,#fff 30%,#c9cbd0 38%,#eef0f3 50%,#b8bbc0 62%,#fff 70%)"></div><div class="label">Marwick Watch</div></div>
  </div>
</section>

<section class="about">
  <div class="ring-back"></div>
  <div class="photo" role="img" aria-label="Pearl ring on a dark background"></div>
  <h2>About Marwick</h2>
  <h3>Stay it with a stone &amp; leave her speechless</h3>
  <div class="copy">
    <p>From “will you?” to “I do” and every momentous occasion in between, Marwick Jewelers offers a radiant array of elegant stones and settings to take her breath away. Our family-owned store here in Ashford, MN upholds this promise we made more than 40 years ago: to provide professional expertise that helps you give a gift with a personal touch.</p>
    <p>Browse our online collection of fine jewelry and then visit us in person. Together we’ll find a piece that speaks from the heart.</p>
  </div>
</section>

<section>
  <h2 class="section-title" style="top:1953px">Custom Design</h2>
  <div class="cards" style="top:2063px">
    <div class="card"><div class="photo" role="img" aria-label="Custom rings with pink coral and amethyst" style="background:linear-gradient(90deg,#3d3f44,#8a8c92 40%,#6b6e74 70%,#2e3035)"></div><div class="label">Custom Pink Coral and Am</div></div>
    <div class="card"><div class="photo" role="img" aria-label="Custom rose gold engagement ring" style="background:linear-gradient(180deg,#4a4e4a,#8f8a80 55%,#c8bfa8)"></div><div class="label">Custom Rose Gold Engagem</div></div>
    <div class="card"><div class="photo" role="img" aria-label="Custom fox pendant" style="background:linear-gradient(180deg,#2a3140 0 8%,#e9e8ec 20%,#f3f2f5)"></div><div class="label">Custom Fox Pendant</div></div>
    <div class="card"><div class="photo" role="img" aria-label="Custom dragonfly pendant with coloured stones" style="background:linear-gradient(135deg,#f1e3c8,#e9d6b4 60%,#d8c09a)"></div><div class="label">Custom Dragonfly Pendant</div></div>
  </div>
</section>

<section class="contact">
  <div class="watch" role="img" aria-label="Two-tone ladies wristwatch"></div>
  <div class="box">
    <h2>Contact Us</h2>
    <div class="field" style="left:42px;top:100px;width:326px;height:75px">First Name</div>
    <div class="field" style="left:373px;top:100px;width:326px;height:75px">Last Name</div>
    <div class="field" style="left:42px;top:184px;width:326px;height:75px">Email</div>
    <div class="field" style="left:373px;top:184px;width:326px;height:75px">Phone</div>
    <div class="field" style="left:42px;top:268px;width:657px;height:150px">Message</div>
    <div class="submit">Contact Us</div>
  </div>
</section>

<footer class="footer">
  <div class="col" style="left:112px"><h4>QUICK LINKS</h4><ul><li>Company</li><li>Custom Jewelery Services</li><li>Jewelery Repair Services</li><li>Resources</li><li>Showcase</li></ul></div>
  <div class="col" style="left:360px"><h4>OTHER LINKS</h4><ul><li>Gallery</li><li>Engraving &amp; Trophies</li><li>Gift Ideas</li></ul></div>
  <div class="col" style="left:590px"><h4>CONTACT</h4><ul class="contact-list" style="margin-top:-6px">
    <li><svg width="13" height="13" viewBox="0 0 24 24"><path fill="#ddd" d="M6.6 10.8a15 15 0 0 0 6.6 6.6l2.2-2.2c.3-.3.7-.4 1-.2 1.1.4 2.3.6 3.6.6.6 0 1 .4 1 1V20c0 .6-.4 1-1 1A17 17 0 0 1 3 4c0-.6.4-1 1-1h3.5c.6 0 1 .4 1 1 0 1.3.2 2.5.6 3.6.1.3 0 .7-.2 1z"/></svg>555-010-2552</li>
    <li><svg width="13" height="13" viewBox="0 0 24 24"><circle cx="12" cy="12" r="10" fill="#ddd"/><path d="M6 9l6 4 6-4" stroke="#434445" stroke-width="2" fill="none"/></svg>dana@marwickjewelers.com</li>
    <li><svg width="13" height="13" viewBox="0 0 24 24"><circle cx="12" cy="12" r="10" fill="#ddd"/><path d="M6 9l6 4 6-4" stroke="#434445" stroke-width="2" fill="none"/></svg>lena@marwickjewelers.com</li>
  </ul></div>
  <div class="col" style="left:889px"><h4>OPENING HOURS</h4><ul class="contact-list" style="margin-top:-6px">
    <li style="font-size:15.5px;line-height:36px"><svg width="13" height="13" viewBox="0 0 24 24" fill="none" stroke="#ddd" stroke-width="3"><circle cx="12" cy="12" r="9"/><path d="M12 7v5h4"/></svg>Mon - Fri: 10am – 07pm</li>
    <li style="font-size:15.5px;line-height:36px"><svg width="13" height="13" viewBox="0 0 24 24" fill="none" stroke="#ddd" stroke-width="3"><circle cx="12" cy="12" r="9"/><path d="M12 7v5h4"/></svg>Sat - Sun: Closed</li>
  </ul></div>
  <div class="rule"></div>
  <div class="copy">© 2022 Marwick Jewellers. All Rights Reserved</div>
  <div class="social"><span><i></i></span><span><i></i></span></div>
</footer>

</body>
</html>
```